Private Dining Restaurant Menu Design

Looking for help in designing a private dining room menu brochure - probably would need 4 panel layout to make all of the content fit, or a 5.5x8" booklet. Open to your ideas on layout/vessel - would want to post on website and be able to print to hand out to guests interested in booking our private dining room.

All content is in the attached "Private Dining Menu".

Would like to match existing dinner menu design - also attached.

Website is www.copperkettlebistro.com

Requirements
Must have
• Easy to read format of a brochure of the private dining menu content - want to be able to hand out to interested guests and have it simple and easy to read/flip through.

```html
<!DOCTYPE html>
<html lang="en">
<head>
<meta charset="utf-8">
<title>Lunch Options</title>
<link rel="stylesheet" href="https://fonts.googleapis.com/css2?family=Audiowide&family=Noto+Serif:ital,wght@0,400;0,700;1,400&display=swap">
<style>
  :root {
    --bg: #26242b;
    --gold-light: #f3dc8c;
    --gold: #d8b25a;
    --gold-dark: #a67c2e;
    --text: #f2efe8;
  }
  * { margin: 0; padding: 0; box-sizing: border-box; }
  html, body { width: 849px; height: 1200px; overflow: hidden; background: var(--bg); }
  .menu-page {
    position: relative;
    width: 849px; height: 1200px;
    background: var(--bg);
    color: var(--text);
    font-family: "Noto Serif", Georgia, serif;
  }
  .page-frame { position: absolute; inset: 0; }
  .page-title {
    position: absolute; top: 94px; left: 0; width: 100%;
    text-align: center;
    font-family: "Audiowide", sans-serif;
    font-size: 46px; letter-spacing: 1px; line-height: 1;
    background: linear-gradient(180deg, var(--gold-light) 0%, var(--gold) 50%, var(--gold-dark) 100%);
    -webkit-background-clip: text; background-clip: text; color: transparent;
  }
  .page-note {
    position: absolute; top: 142px; left: 0; width: 100%;
    text-align: center; font-size: 15.5px;
  }
  .option { position: absolute; left: 70px; width: 700px; }
  .option-title { font-weight: 700; font-size: 18.5px; line-height: 22px; }
  .option-desc { font-style: italic; font-size: 14.6px; line-height: 20px; margin-top: 3px; }
  .option-list { list-style: none; margin-top: 22px; font-size: 14.9px; }
  .option-list li { position: relative; padding-left: 26px; line-height: 21.5px; }
  .option-list li::before { content: "•"; position: absolute; left: 2px; top: 0; }
  .option-a { top: 186px; }
  .option-b { top: 365px; }
  .option-b .option-list li { line-height: 22px; }
  .option-c { top: 566px; }
  .option-c .option-list li { line-height: 22px; }
  .room-photo {
    position: absolute; left: 365px; top: 679px; width: 385px; height: 384px;
    background: linear-gradient(160deg, #6d6258 0%, #4a4038 40%, #8a7b68 75%, #5a4e43 100%);
  }
  .accent-bar-vertical {
    position: absolute; left: 329px; top: 679px; width: 9px; height: 416px;
    background: linear-gradient(90deg, var(--gold-dark), var(--gold-light), var(--gold-dark));
  }
  .accent-bar-horizontal {
    position: absolute; left: 365px; top: 1098px; width: 385px; height: 5px;
    background: linear-gradient(180deg, var(--gold-light), var(--gold-dark));
  }
</style>
</head>
<body>
<div class="menu-page">
  <svg class="page-frame" width="849" height="1200" viewBox="0 0 849 1200" aria-hidden="true">
    <defs>
      <linearGradient id="frameGold" x1="0" y1="0" x2="1" y2="1">
        <stop offset="0" stop-color="#f3dc8c"/>
        <stop offset="0.5" stop-color="#c99a45"/>
        <stop offset="1" stop-color="#f0d383"/>
      </linearGradient>
    </defs>
    <path d="M44 16 L803 16 A30 30 0 0 0 833 46 L833 1154 A30 30 0 0 0 803 1184 L44 1184 A30 30 0 0 0 14 1154 L14 46 A30 30 0 0 0 44 16 Z"
          fill="none" stroke="url(#frameGold)" stroke-width="2.5"/>
    <path d="M52 26 L795 26 A26 26 0 0 0 821 52 L821 1148 A26 26 0 0 0 795 1174 L52 1174 A26 26 0 0 0 26 1148 L26 52 A26 26 0 0 0 52 26 Z"
          fill="none" stroke="url(#frameGold)" stroke-width="1.5"/>
  </svg>

  <h1 class="page-title">LUNCH OPTIONS</h1>
  <p class="page-note">(an option must be chosen for groups of 15 or more, served before 3pm)</p>

  <section class="option option-a">
    <h2 class="option-title">Option A - $10-$12/Person</h2>
    <p class="option-desc">Pick Two Lunch Menu – Soup/Salad ($10), Soup/Sandwich ($11), or Salad/Sandwich ($12)</p>
    <ul class="option-list">
      <li>Sandwiches: ½ Turkey Club, ½ BLTA, &nbsp;BBQ Pork Sliders (2), Wood-Roasted Rotisserie Chicken Sliders (2), Walleye Tacos (2), or Chicken Tacos (2)</li>
      <li>Soups: Chicken Wild Rice, White Chicken Chili, or Soup of the Day</li>
      <li>Salads: Wedge, House, or Caesar Salad</li>
    </ul>
  </section>

  <section class="option option-b">
    <h2 class="option-title">Option B - $13/Person</h2>
    <p class="option-desc">Served with your choice of fries, cheesy hashbrowns, soup, or apple cabbage slaw</p>
    <ul class="option-list">
      <li>Applewood Bacon &amp; Fajita Chicken Salad</li>
      <li>Rotisserie Chicken Salad</li>
      <li>Brown Sugar Bacon and Smoked Cheddar Burger</li>
      <li>Pepperjack Turkey Melt</li>
      <li>Walleye Fish Tacos</li>
    </ul>
  </section>

  <section class="option option-c">
    <h2 class="option-title">Option C - $13/Person Buffet Option</h2>
    <p class="option-desc">Food ready upon arrival, or at a set time of your choice</p>
    <ul class="option-list">
      <li>Sandwich platter – Assorted Rotisserie Turkey Club, Ham and Cheese, and Veggie Wrap</li>
      <li>Rotisserie Chicken Salad Bar</li>
      <li>Fresh Fruit Platter</li>
      <li>House-made Potato Chips</li>
    </ul>
  </section>

  <div class="accent-bar-vertical"></div>
  <div class="room-photo" role="img" aria-label="Photo of the private dining room with set tables, stone fireplace and pendant lights"></div>
  <div class="accent-bar-horizontal"></div>
</div>
</body>
</html>
```